KAJU Freightways #ALLKAJU Business Cards & Letterhead

I am looking to business cards designed for our organization. We are currently undergoing a small re-branding that is taking place. Our organization is called KAJU Freightways and we are headquartered in Phoenix, AZ. We primarily provide transportation and logistics services to the Marlow Parcel Bureau who is our largest customer. I would like to see a design that incorporates name, title, contact info, website, and address (this will be different depending on the employee). I would also like to see some color on the business card using our logo colors or a variation. I would like our logo on the back of the business card with the website displayed. The final design should communicate that we are a next generation transportation operate that focuses on being driver-first, customer-centric, innovative, and sustainable.We would also like our #ALLKAJU catch phrase incorporated as well.

Target Market(s)

Transportation & Logistics

Industry/Entity Type

Trucking Company

Contact Information for Business Card

-First and Last Name
-Position Title
-Contact Phone
-Contact Email
-Physical Address

Font styles to use
Serif

Colors

Designer to choose colors to be used in the design.

Requirements
Must have
• -KAJU logo prominently displayed
• -#ALLKAJU catch phrase used
• -Some amount of color, design gradient, etc.
• -Logo on the back with website listed (https://www.kajufreightco.example)

```html
<!DOCTYPE html>
<html lang="en">
<head>
<meta charset="utf-8">
<title>KAJU Freightways – Letterhead &amp; Business Cards</title>
<link rel="stylesheet" href="https://fonts.googleapis.com/css2?family=Lato:wght@400;700&family=Arimo:wght@400;700&display=swap">
<style>
:root{
  --bg:#e4e4e4;
  --paper:#f5f5f5;
  --teal:#163a45;
  --green:#7aba42;
  --ink:#1a1a1a;
}
*{margin:0;padding:0;box-sizing:border-box}
html,body{width:1200px;height:1200px;overflow:hidden}
body{background:var(--bg);position:relative;font-family:'Lato',sans-serif}

.letterhead{position:absolute;left:88px;top:145px;width:696px;height:901px;background:var(--paper);box-shadow:2px 2px 4px rgba(0,0,0,.25)}

.brand{position:absolute;display:flex;align-items:center;font-family:'Lato',sans-serif;font-weight:700;color:var(--teal);line-height:1;white-space:nowrap}
.brand .dot{display:block;border-radius:50%;background:var(--green);flex:none}
.letterhead .brand{left:53px;top:74px;font-size:30px;gap:8px}
.letterhead .brand .dot{width:14px;height:14px}
.divider{position:absolute;width:2px;background:var(--teal)}
.letterhead .divider{left:161px;top:41px;height:97px}
.tagline{position:absolute;color:var(--green);font-family:'Lato',sans-serif;line-height:1.2}
.letterhead .tagline{left:177px;top:70px;font-size:17px}

.sender{position:absolute;right:52px;top:48px;text-align:right;color:var(--teal);font-size:10px;line-height:12.3px;font-style:normal}
.sender strong{font-weight:700}
.sender .contact{margin-top:6px}
.icon{display:inline-block;vertical-align:-1px;margin-left:3px}

.letter{position:absolute;left:53px;top:230px;width:596px;font-family:'Arimo',sans-serif;font-size:9.4px;line-height:13.7px;color:var(--ink)}
.letter .date{margin-bottom:13px}
.letter .recipient{margin-bottom:25px}
.letter .salutation{font-weight:700;margin-bottom:27px}
.letter p.body{text-align:justify;margin-bottom:13.5px}
.letter .closing{margin-top:35px}
.signature{width:140px;height:22px;margin:14px 0 10px;background:linear-gradient(90deg,#cfcfcf,#e2e2e2);border-radius:3px}

.footer{position:absolute;left:0;bottom:0;width:100%;height:23px}
.footer svg{position:absolute;inset:0}
.footer .hashtag{position:absolute;left:53px;top:4px;color:var(--paper);font-size:11px;font-weight:700}
.footer .hashtag span{color:var(--green)}
.footer .site{position:absolute;right:53px;top:4px;color:#fff;font-size:11px}

.card{position:absolute;left:836px;width:287px;height:164px;box-shadow:2px 2px 4px rgba(0,0,0,.25);overflow:hidden}
.card-back{top:271px;background:var(--teal)}
.card-back .pattern{position:absolute;inset:0;background:radial-gradient(circle at 50% 50%,#1b4551 0%,#173d48 70%)}
.card-back .brand{left:0;right:0;top:70px;justify-content:center;font-size:26px;gap:8px;color:#fff}
.card-back .brand .dot{width:12px;height:12px}
.card-back .site{position:absolute;left:0;right:0;top:137px;text-align:center;color:#fff;font-size:7.5px;letter-spacing:.6px}
.card-back .site span{color:var(--green)}

.card-front{top:460px;background:var(--paper)}
.card-front .brand{left:19px;top:41px;font-size:13px;gap:4px}
.card-front .brand .dot{width:7px;height:7px}
.card-front .divider{left:74px;top:20px;height:49px;width:1px}
.card-front .tagline{left:83px;top:34px;font-size:8px}
.card-front .person{position:absolute;right:18px;top:35px;text-align:right}
.card-front .person .name{color:var(--green);font-size:10.5px;font-weight:700}
.card-front .person .title{color:var(--teal);font-size:7px}
.card-front .details{position:absolute;left:20px;top:88px;color:var(--teal);font-size:7px;line-height:9.6px}
.card-front .details strong{font-weight:700}
.card-front .details .contact{margin-top:4px}
.card-front .footer{height:13px}
.card-front .footer .hashtag{left:20px;top:1px;font-size:7.5px}
.card-front .footer .site{right:18px;top:2px;font-size:6.8px}
</style>
</head>
<body>

<section class="letterhead">
  <div class="brand"><span class="dot"></span>KAJU</div>
  <div class="divider"></div>
  <div class="tagline">Transportation<br>and Energy Services</div>

  <address class="sender">
    <strong>KAJU Freightways &amp; Energy Services, Inc.</strong><br>
    4410 North Saguaro Ridge Road<br>
    Mesa, AZ 85201
    <div class="contact">
      480-555-0142<svg class="icon" width="9" height="9" viewBox="0 0 24 24"><path fill="#7aba42" d="M6.6 10.8a15.1 15.1 0 0 0 6.6 6.6l2.2-2.2a1 1 0 0 1 1-.25 11.4 11.4 0 0 0 3.6.6 1 1 0 0 1 1 1V20a1 1 0 0 1-1 1A17 17 0 0 1 3 4a1 1 0 0 1 1-1h3.5a1 1 0 0 1 1 1c0 1.25.2 2.45.6 3.6a1 1 0 0 1-.25 1z"/></svg><br>
      info@kajufreightco.example<svg class="icon" width="10" height="8" viewBox="0 0 20 14"><rect x="1" y="1" width="18" height="12" fill="none" stroke="#7aba42" stroke-width="2"/><path d="M1 1l9 7 9-7" fill="none" stroke="#7aba42" stroke-width="2"/></svg>
    </div>
  </address>

  <div class="letter">
    <div class="date">November 15, 2019</div>
    <div class="recipient">Mr. John Doe<br>President<br>AA Corporation<br>111 Street Name, Suite#<br>City, State, 12345</div>
    <div class="salutation">Dear Mr. John,</div>
    <p class="body">Lorem ipsum dolor sit amet, consectetur adipiscing elit. Integer diam quam, egestas eu ultrices eu, suscipit ac sapien. Phasellus eu dui nisi. Nam et euismod diam, nec lobortis tortor. Donec et diam nulla. Aenean varius tincidunt convallis. Aliquam a tortor at lacus dictum aliquet. Nunc laoreet metus sapien, in scelerisque augue consectetur in.</p>
    <p class="body">Fusce nec justo laoreet, egestas justo sed, aliquet sem. Pellentesque pharetra massa non orci bibendum semper. Pellentesque cursus eu lectus a consectetur. Nunc volutpat suscipit posuere. Vestibulum facilisis vel quam malesuada mattis. Nulla in mattis tellus. Maecenas tristique mauris vitae pharetra tincidunt. In ut ornare risus. Integer molestie vestibulum nisi, semper dapibus mi condimentum eu.</p>
    <p class="body">Nullam sagittis elit libero, id fringilla est tincidunt eget. Donec in ipsum ultricies, consectetur quam vel, facilisis elit. Phasellus tincidunt congue risus vel luctus. Suspendisse ut mollis neque. Donec ornare orci in turpis vestibulum, in ultrices metus scelerisque. Pellentesque mattis mattis nunc, nec tincidunt lacus egestas id. Fusce facilisis sagittis neque sit amet vulputate. Aliquam ut eros lobortis tortor facilisis vehicula. Sed sed luctus leo, at laoreet sapien. Donec placerat adipiscing ligula non euismod. In lobortis pretium nisl id luctus.</p>
    <p class="body">Integer gravida tincidunt nibh, scelerisque tincidunt turpis. Suspendisse potenti. Nunc hendrerit euismod lectus id elementum. Fusce vitae gravida velit, quis eleifend lectus. In imperdiet mauris eu dui viverra sagittis. Donec tempor dui diam, condimentum gravida lacus pretium a. Nullam fringilla augue quis arcu placerat scelerisque. Aliquam nec tincidunt augue, sit amet posuere ipsum.</p>
    <div class="closing">Sincerely Yours,</div>
    <div class="signature" role="img" aria-label="Handwritten signature of Renata Holloway"></div>
    <div>Renata Holloway<br>President</div>
  </div>

  <div class="footer">
    <svg width="696" height="23" viewBox="0 0 696 23" preserveAspectRatio="none">
      <polygon points="0,0 483,0 472,23 0,23" fill="#163a45"/>
      <polygon points="487,0 696,0 696,23 476,23" fill="#7aba42"/>
    </svg>
    <div class="hashtag"><span>#</span>ALLKAJU</div>
    <div class="site">www.kajufreightco.example</div>
  </div>
</section>

<section class="card card-back">
  <div class="pattern"></div>
  <div class="brand"><span class="dot"></span>KAJU</div>
  <div class="site">www.<span>kajufreightco</span>.example</div>
</section>

<section class="card card-front">
  <div class="brand"><span class="dot"></span>KAJU</div>
  <div class="divider"></div>
  <div class="tagline">Transportation<br>and Energy Services</div>
  <div class="person">
    <div class="name">RENATA HOLLOWAY</div>
    <div class="title">President</div>
  </div>
  <div class="details">
    <strong>KAJU Freightways &amp; Energy Services, Inc.</strong><br>
    4410 North Saguaro Ridge Road<br>
    Mesa, AZ 85201
    <div class="contact">
      <svg width="6" height="6" viewBox="0 0 24 24"><path fill="#7aba42" d="M6.6 10.8a15.1 15.1 0 0 0 6.6 6.6l2.2-2.2a1 1 0 0 1 1-.25 11.4 11.4 0 0 0 3.6.6 1 1 0 0 1 1 1V20a1 1 0 0 1-1 1A17 17 0 0 1 3 4a1 1 0 0 1 1-1h3.5a1 1 0 0 1 1 1c0 1.25.2 2.45.6 3.6a1 1 0 0 1-.25 1z"/></svg> 480-555-0142<br>
      <svg width="7" height="5" viewBox="0 0 20 14"><rect x="1" y="1" width="18" height="12" fill="none" stroke="#7aba42" stroke-width="2"/><path d="M1 1l9 7 9-7" fill="none" stroke="#7aba42" stroke-width="2"/></svg> renata@kajufreightco.example
    </div>
  </div>
  <div class="footer">
    <svg width="287" height="13" viewBox="0 0 287 13" preserveAspectRatio="none">
      <polygon points="0,0 171,0 166,13 0,13" fill="#163a45"/>
      <polygon points="173,0 287,0 287,13 168,13" fill="#7aba42"/>
    </svg>
    <div class="hashtag"><span>#</span>ALLKAJU</div>
    <div class="site">www.kajufreightco.example</div>
  </div>
</section>

</body>
</html>
```